Business Card Design

New business card design

Target Market(s)

Residential & Commercial Property Managers

Industry/Entity Type

Plumbing Services

Contact Information for Business Card

Name - Rowan Keddle, title - Director, Phone Number - 0431 286 517, email - rowan@tbk-plumbing.com.au, Company ABN - 73 215 904 386,

Font styles to use
Sans Serif

Colors
0054AA
0677BA
7BADD7
CADEEF
E8F1F8

```html
<!DOCTYPE html>
<html lang="en">
<head>
<meta charset="utf-8">
<title>TBK Plumbing Services – Business Card</title>
<link href="https://fonts.googleapis.com/css2?family=Montserrat:wght@300;400;600;700&display=swap" rel="stylesheet">
<style>
  :root {
    --deep-blue: #0054AA;
    --mid-blue: #0677BA;
    --soft-blue: #7BADD7;
    --pale-blue: #CADEEF;
    --mist-blue: #E8F1F8;
    --bright-blue: #1AA7E6;
    --navy: #003C85;
    --taupe: #7A6E64;
    --paper: #F7F7F5;
    --ink: #1E1E1E;
    --stage: #1C1C1C;
  }
  * { box-sizing: border-box; margin: 0; padding: 0; }
  html, body { width: 1200px; height: 852px; overflow: hidden; }
  body {
    background: var(--stage);
    font-family: "Montserrat", sans-serif;
    position: relative;
  }
  .card {
    position: absolute;
    top: 283px;
    width: 500px;
    height: 286px;
    border-radius: 22px;
    overflow: hidden;
  }
  .card-front { left: 70px; background: var(--mid-blue); }
  .card-back { left: 630px; background: var(--paper); }
  .card-art { position: absolute; inset: 0; width: 100%; height: 100%; }

  .brand {
    position: absolute;
    display: flex;
    flex-direction: column;
    font-weight: 300;
  }
  .brand-name { font-size: 64px; letter-spacing: 2px; line-height: 1; }
  .brand-tag { font-size: 13px; letter-spacing: 9px; margin-top: 6px; }
  .card-front .brand {
    color: #fff;
    left: 0; right: 0; top: 88px;
    align-items: center;
  }
  .card-back .brand {
    color: var(--ink);
    left: 28px; top: 28px;
  }
  .card-back .brand-name { font-size: 52px; }
  .card-back .brand-tag { font-size: 11px; letter-spacing: 7px; }

  .contact {
    position: absolute;
    left: 30px; top: 146px;
    color: #fff;
  }
  .contact-name { font-size: 19px; font-weight: 700; }
  .contact-title { font-size: 11px; font-weight: 400; color: var(--pale-blue); margin-bottom: 8px; }
  .contact-list { list-style: none; }
  .contact-list li {
    display: flex; align-items: center; gap: 10px;
    font-size: 11px; line-height: 17px; color: var(--mist-blue);
  }
  .contact-list svg { width: 11px; height: 11px; flex: none; }
  .location {
    position: absolute;
    left: 30px; bottom: 8px;
    font-size: 11px; color: var(--mist-blue); letter-spacing: .5px;
  }
</style>
</head>
<body>

<section class="card card-front" aria-label="Card front">
  <svg class="card-art" viewBox="0 0 500 286" preserveAspectRatio="none" aria-hidden="true">
    <defs>
      <linearGradient id="front-sky" x1="0" y1="0" x2="0" y2="1">
        <stop offset="0" stop-color="#3FB0DE"/>
        <stop offset="1" stop-color="var(--mid-blue)"/>
      </linearGradient>
    </defs>
    <rect width="500" height="286" fill="url(#front-sky)"/>
    <path d="M0 110 C120 60 260 40 500 70 L500 286 L0 286 Z" fill="#1F8ACB" opacity=".8"/>
    <path d="M0 150 C140 110 300 90 500 110 L500 286 L0 286 Z" fill="var(--mid-blue)"/>
    <path d="M0 200 C160 150 330 150 500 170 L500 286 L0 286 Z" fill="var(--deep-blue)"/>
    <path d="M0 250 C170 210 340 215 500 230 L500 286 L0 286 Z" fill="var(--navy)"/>
  </svg>
  <div class="brand">
    <span class="brand-name">TBK</span>
    <span class="brand-tag">plumbing services</span>
  </div>
</section>

<section class="card card-back" aria-label="Card back">
  <svg class="card-art" viewBox="0 0 500 286" preserveAspectRatio="none" aria-hidden="true">
    <path d="M0 128 C120 112 260 120 360 150 L500 180 L500 286 L0 286 Z" fill="var(--mid-blue)"/>
    <path d="M0 170 C140 150 280 165 420 200 L500 215 L500 286 L0 286 Z" fill="var(--deep-blue)"/>
    <path d="M0 215 C150 200 300 215 500 240 L500 286 L0 286 Z" fill="var(--navy)"/>
    <path d="M0 254 L500 196 L500 286 L0 286 Z" fill="var(--taupe)"/>
    <circle cx="420" cy="90" r="120" fill="var(--paper)"/>
    <circle cx="420" cy="90" r="104" fill="var(--bright-blue)"/>
  </svg>
  <div class="brand">
    <span class="brand-name">TBK</span>
    <span class="brand-tag">plumbing services</span>
  </div>
  <div class="contact">
    <p class="contact-name">Rowan Keddle</p>
    <p class="contact-title">Managing Director</p>
    <ul class="contact-list">
      <li>
        <svg viewBox="0 0 12 12"><path d="M1 3 Q6 0 11 3 L10 5 L8 4.5 L8 3.5 Q6 3 4 3.5 L4 4.5 L2 5 Z M3 6 H9 L10 11 H2 Z" fill="#fff"/></svg>
        0431 286 517
      </li>
      <li>
        <svg viewBox="0 0 12 12"><rect x="1" y="2.5" width="10" height="7" fill="#fff"/><path d="M1 2.5 L6 7 L11 2.5" fill="none" stroke="var(--deep-blue)" stroke-width="1"/></svg>
        rowan@tbk-plumbing.com.au
      </li>
      <li>
        <svg viewBox="0 0 12 12"><circle cx="6" cy="6" r="5" fill="none" stroke="#fff" stroke-width="1.2"/><ellipse cx="6" cy="6" rx="2" ry="5" fill="none" stroke="#fff"/><path d="M1 6 H11" stroke="#fff"/></svg>
        www.tbk-plumbing.com.au
      </li>
      <li>
        <svg viewBox="0 0 12 12"><path d="M4 1 L3 11 M8 1 L7 11 M1 4 H11 M1 8 H11" stroke="#fff" stroke-width="1.3"/></svg>
        ABN - 73 215 904 386
      </li>
    </ul>
  </div>
  <p class="location">Sydney | NSW | Australia</p>
</section>

</body>
</html>
```